Thornvale Agribusiness Consulting needs a Website Design.

We need a website design for a new company based in UK. Thornvale offers agribusiness consulting and farm design services to farmers, smallholders and the wider agribusiness industry to assist clients in adopting more sustainable and regenerative production, processing and marketing practices.
Services are offered face-to-face and on a remote platform.
Services are offered in the UK and overseas.
We would like to see designs that reflect the natural environment, business and sustainability. Desired colours; green, blue, grey. The final design should communicate professionalism in the rural economy.
The design should be able to be customized by the client to make future changes and additions.
Target Market(s)
Farmers, smallholders, and the agricultural industry in UK and overseas.
Industry/Entity Type
Agribusiness
Number of Pages Required
4 page
Look and feel
Each slider illustrates characteristics of the customer's brand and the style your logo design should communicate.

```html
<!DOCTYPE html>
<html lang="en">
<head>
<meta charset="utf-8">
<title>Thornvale Agribusiness Consulting</title>
<link rel="stylesheet" href="https://fonts.googleapis.com/css2?family=Questrial&family=Open+Sans:wght@400;600&display=swap">
<style>
  :root{
    --teal:#1fb89c;
    --teal-dark:#13a086;
    --lime:#9ccc3c;
    --lime-dark:#7fb52a;
    --sky:#4cc4ec;
    --ink:#1e1e1e;
    --text:#555;
    --pale:#eeeeee;
    --pill:#efefef;
    --band:#3a3a3a;
    --foot:#1b1b1b;
    --foot-text:#bdbdbd;
    --foot-muted:#6d6d6d;
    --ring-blue:#7cc6e4;
    --ring-teal:#86d0c6;
    --ring-lime:#c7e27a;
  }
  *{box-sizing:border-box;margin:0;padding:0}
  html,body{width:816px;height:1200px;overflow:hidden;background:#fff}
  body{position:relative;font-family:"Open Sans",Arial,sans-serif;color:var(--text)}
  .abs{position:absolute}
  .heading{font-family:"Questrial",Arial,sans-serif;text-transform:uppercase;color:var(--ink)}

  /* header */
  .site-header{left:0;top:0;width:816px;height:95px;background:#fff}
  .brand{display:flex;align-items:center;gap:8px;font-family:"Questrial",Arial,sans-serif;font-size:24px;color:var(--ink)}
  .brand-dot{width:16px;height:16px;border-radius:50%;background:var(--lime)}
  .contact-pill{top:13px;height:25px;border-radius:13px;background:var(--pill);display:flex;align-items:center;font-size:12px;color:#444}
  .contact-pill .icon{width:25px;height:25px;border-radius:50%;background:var(--lime);display:flex;align-items:center;justify-content:center;margin-right:7px}
  .main-nav{left:290px;top:57px;width:476px;height:28px;border-radius:14px;background:linear-gradient(#3fd0b4,var(--teal-dark));display:flex;box-shadow:0 1px 2px rgba(0,0,0,.2)}
  .main-nav a{font-family:"Questrial",Arial,sans-serif;font-size:11px;color:#fff;text-decoration:none;display:flex;align-items:center;justify-content:center;border-right:1px solid rgba(0,0,0,.12)}
  .main-nav a:last-child{border-right:0}

  /* hero */
  .hero{left:0;top:95px;width:816px;height:363px;background:linear-gradient(#c9ced3 0%,#9ea6ad 62%,#5b6b5a 80%,#6f9a3c 84%,#7ea747 100%)}
  .hero-arrow{top:265px;width:24px;height:24px;background:#fff;display:flex;align-items:center;justify-content:center}

  /* welcome */
  .welcome{left:0;top:458px;width:816px;height:228px;background:var(--pale)}
  .welcome h1{position:absolute;left:0;width:816px;top:40px;text-align:center;font-size:17px;font-weight:400;letter-spacing:.2px}
  .welcome p{position:absolute;left:112px;width:592px;top:78px;text-align:center;font-size:10.3px;line-height:17.6px;color:#555}
  .btn-pill{border-radius:10px;background:linear-gradient(#b9e06a,var(--lime-dark));color:#2d3d10;font-family:"Questrial",Arial,sans-serif;text-transform:uppercase;font-size:9px;display:flex;align-items:center;justify-content:center}

  /* services */
  .service{top:718px;width:180px;text-align:center}
  .service svg{display:block;margin:0 auto}
  .service h2{margin-top:14px;font-size:15px;font-weight:400}

  /* newsletter */
  .newsletter{left:0;top:947px;width:816px;height:63px;background:var(--band)}
  .newsletter-title{left:106px;top:963px;font-family:"Questrial",Arial,sans-serif;font-size:14px;line-height:14px;color:#fff;text-transform:uppercase}
  .field{top:968px;width:164px;height:22px;background:#fff;border-radius:2px;font-size:9px;color:#999;padding:5px 6px}
  .follow{left:661px;top:942px;width:104px;height:68px;background:var(--sky);text-align:center;color:#fff;font-family:"Questrial",Arial,sans-serif;font-size:11px;padding-top:9px}
  .follow-dot{width:32px;height:32px;border-radius:50%;background:#fff;margin:6px auto 0}

  /* footer */
  .site-footer{left:0;top:1010px;width:816px;height:190px;background:var(--foot)}
  .legal{left:50px;top:1136px;font-size:8px;line-height:13px;color:var(--foot-muted)}
  .col-title{top:1039px;font-family:"Questrial",Arial,sans-serif;font-size:11px;color:#fff;text-transform:uppercase}
  .post{width:166px}
  .post .meta{font-size:8px;color:var(--foot-muted)}
  .post .title{margin-top:5px;font-size:9.6px;line-height:13px;color:var(--foot-text)}
  .divider{width:166px;height:1px;background:#2e2e2e}
  .touch{left:601px;display:flex;gap:9px;font-size:9px;line-height:13px;color:var(--foot-text)}
  .touch .icon{width:22px;height:22px;border-radius:50%;background:#4a4a4a;flex:none;display:flex;align-items:center;justify-content:center}
</style>
</head>
<body>

<header class="site-header abs">
  <div class="brand abs" style="left:68px;top:32px"><span class="brand-dot"></span>Thornvale</div>

  <div class="contact-pill abs" style="left:447px;width:146px">
    <span class="icon"><svg width="12" height="12" viewBox="0 0 24 24"><path fill="#2f4a0c" d="M6.6 10.8a15.2 15.2 0 0 0 6.6 6.6l2.2-2.2c.3-.3.7-.4 1-.2 1.1.4 2.3.6 3.6.6.6 0 1 .4 1 1V20c0 .6-.4 1-1 1A17 17 0 0 1 3 4c0-.6.4-1 1-1h3.5c.6 0 1 .4 1 1 0 1.3.2 2.5.6 3.6.1.3 0 .7-.2 1z"/></svg></span>
    (+44) 01632 960418
  </div>
  <div class="contact-pill abs" style="left:606px;width:160px">
    <span class="icon"><svg width="12" height="12" viewBox="0 0 24 24"><path fill="#2f4a0c" d="M3 9l9-6 9 6v11H3zM5 10l7 5 7-5"/></svg></span>
    hello@thornvale.co.uk
  </div>

  <nav class="main-nav abs">
    <a href="#" style="width:92px">HOME</a>
    <a href="#" style="width:88px">ABOUT US</a>
    <a href="#" style="width:100px">WHAT WE DO</a>
    <a href="#" style="width:84px">SERVICES</a>
    <a href="#" style="width:112px">CONTACT</a>
  </nav>
</header>

<section class="hero abs" role="img" aria-label="Large oak tree standing alone in a green field under a cloudy grey sky"></section>
<div class="hero-arrow abs" style="left:0"><svg width="8" height="10" viewBox="0 0 8 10"><path d="M6 1L2 5l4 4" fill="none" stroke="#333" stroke-width="1.6"/></svg></div>
<div class="hero-arrow abs" style="left:792px"><svg width="8" height="10" viewBox="0 0 8 10"><path d="M2 1l4 4-4 4" fill="none" stroke="#333" stroke-width="1.6"/></svg></div>

<section class="welcome abs">
  <h1 class="heading">Welcome to Thornvale</h1>
  <p>Nam liber tempor cum soluta nobis eleifend option congue nihil imperdiet doming id quod mazim placerat facer possim assum. Typi non habent claritatem insitam; est usus legentis in iis qui facit eorum claritatem. Claritas est etiam processus dynamicus, qui sequitur mutationem consuetudium lectorum. Mirum est notare quam littera gothica, quam nunc putamus parum claram, anteposuerit litterarum formas humanitatis per seacula quarta decima et quinta decima. Eodem modo typi, qui nunc nobis videntur parum clari, fiant sollemnes in futurum.</p>
  <a class="btn-pill abs" href="#" style="left:371px;top:180px;width:75px;height:18px;text-decoration:none">Learn More</a>
</section>

<section>
  <div class="service abs" style="left:81px">
    <svg width="170" height="170" viewBox="0 0 170 170">
      <circle cx="83" cy="85" r="84" fill="var(--ring-blue)"/>
      <circle cx="90" cy="85" r="80" fill="#fff"/>
      <circle cx="90" cy="85" r="75" fill="#6a8f4a" role="img" aria-label="Herd of cows grazing in a green pasture"/>
    </svg>
    <h2 class="heading">Consulting</h2>
  </div>
  <div class="service abs" style="left:326px">
    <svg width="170" height="170" viewBox="0 0 170 170">
      <circle cx="83" cy="85" r="84" fill="var(--ring-teal)"/>
      <circle cx="90" cy="85" r="80" fill="#fff"/>
      <circle cx="90" cy="85" r="75" fill="#dcdcd8" role="img" aria-label="Tray of fresh white eggs"/>
    </svg>
    <h2 class="heading">Production</h2>
  </div>
  <div class="service abs" style="left:572px">
    <svg width="170" height="170" viewBox="0 0 170 170">
      <circle cx="83" cy="85" r="84" fill="var(--ring-lime)"/>
      <circle cx="90" cy="85" r="80" fill="#fff"/>
      <circle cx="90" cy="85" r="75" fill="#b0683e" role="img" aria-label="Local market stall with fresh vegetables"/>
    </svg>
    <h2 class="heading">Marketing</h2>
  </div>
</section>

<section class="newsletter abs"></section>
<svg class="abs" style="left:48px;top:966px" width="52" height="26" viewBox="0 0 52 26"><path d="M14 3h36v20H14zM14 3l18 12L50 3" fill="none" stroke="#5a5a5a" stroke-width="2"/><path d="M2 9h8M4 14h6M2 19h8" stroke="#5a5a5a" stroke-width="2"/></svg>
<div class="newsletter-title abs">Subscribe<br>Our Newsletter</div>
<div class="field abs" style="left:226px">Enter Your Name</div>
<div class="field abs" style="left:397px">Enter Your Email</div>
<div class="btn-pill abs" style="left:567px;top:968px;width:75px;height:22px;border-radius:3px;font-size:10px">Subscribe</div>
<div class="follow abs">FOLLOW US ON<div class="follow-dot"></div></div>

<footer class="site-footer abs"></footer>
<div class="brand abs" style="left:65px;top:1086px;color:#fff"><span class="brand-dot"></span>Thornvale</div>
<div class="legal abs">© 2015 Thornvale. All Rights Reserved<br>Terms and Conditions | Privacy Policy |<br>Terms of Use</div>

<div class="col-title abs" style="left:233px">Recent Blog</div>
<div class="post abs" style="left:233px;top:1065px"><div class="meta">10 MAR 2015 | 10 Comments</div><div class="title">Mirum est notare quam littera gothi ca, quam nunc</div></div>
<div class="divider abs" style="left:233px;top:1119px"></div>
<div class="post abs" style="left:233px;top:1137px"><div class="meta">10 MAR 2015 | 10 Comments</div><div class="title">Mirum est notare quam littera gothi ca, quam nunc</div></div>

<div class="col-title abs" style="left:417px">Recent News</div>
<div class="post abs" style="left:417px;top:1065px"><div class="meta">10 MAR 2015</div><div class="title">Mirum est notare quam littera gothi ca, quam nunc</div></div>
<div class="divider abs" style="left:417px;top:1119px"></div>
<div class="post abs" style="left:417px;top:1137px"><div class="meta">10 MAR 2015</div><div class="title">Mirum est notare quam littera gothi ca, quam nunc</div></div>

<div class="col-title abs" style="left:601px">Get in Touch</div>
<div class="touch abs" style="top:1064px">
  <span class="icon"><svg width="10" height="12" viewBox="0 0 10 12"><path d="M5 0a4 4 0 0 0-4 4c0 3 4 8 4 8s4-5 4-8a4 4 0 0 0-4-4z" fill="#ddd"/><circle cx="5" cy="4" r="1.5" fill="#4a4a4a"/></svg></span>
  <span>228, Lorem ipsum dolor amet<br>sit aremt sor- 859584</span>
</div>
<div class="touch abs" style="top:1106px">
  <span class="icon"><svg width="11" height="11" viewBox="0 0 24 24"><path fill="#ddd" d="M6.6 10.8a15.2 15.2 0 0 0 6.6 6.6l2.2-2.2c.3-.3.7-.4 1-.2 1.1.4 2.3.6 3.6.6.6 0 1 .4 1 1V20c0 .6-.4 1-1 1A17 17 0 0 1 3 4c0-.6.4-1 1-1h3.5c.6 0 1 .4 1 1 0 1.3.2 2.5.6 3.6.1.3 0 .7-.2 1z"/></svg></span>
  <span>Phone :<br>(+44) 01632 960418</span>
</div>
<div class="touch abs" style="top:1150px">
  <span class="icon"><svg width="11" height="11" viewBox="0 0 24 24"><path fill="#ddd" d="M3 9l9-6 9 6v11H3z"/></svg></span>
  <span>Email :<br>hello@thornvale.co.uk</span>
</div>

</body>
</html>
```